I am looking for a modern, clean and neat design for a reflexology and well being business. The business name is Gralo Tund (this is an old Latin word for wellbeing). The colours I would like are purple, white and grey. I am open to suggestions for pictures such as healing or working hands, a pair of feet, images that represent my business that you may think of....... or maybe you think no images at all would be best? My tag line is: "Relax, Renew, Revive" or "Find you balance......... Relax, Renew, Revive" I can decide which I want so I would like to see what both would look like. I would like space on the back to write the client's appointment date and time (more than once)

```html
<!DOCTYPE html>
<html lang="en">
<head>
<meta charset="utf-8">
<title>Gralo Tund – Business Cards</title>
<link href="https://fonts.googleapis.com/css2?family=Open+Sans:wght@400;600;700&display=swap" rel="stylesheet">
<style>
  :root {
    --backdrop: #e9e7e4;
    --card: #ffffff;
    --ink: #3d3d3f;
    --ink-soft: #555558;
    --purple: #9b19b5;
    --dots: #555558;
  }
  * { box-sizing: border-box; margin: 0; padding: 0; }
  html, body {
    width: 1200px; height: 900px; overflow: hidden;
    background: var(--backdrop);
    font-family: "Open Sans", Arial, sans-serif;
    color: var(--ink);
  }
  .sheet {
    position: relative; width: 1200px; height: 900px;
    display: flex; flex-direction: column; align-items: center; justify-content: center; gap: 34px;
  }
  .card {
    position: relative; width: 700px; height: 400px;
    background: var(--card);
    box-shadow: 0 6px 18px rgba(0,0,0,.14);
    overflow: hidden;
  }

  /* Shared brand lockup */
  .brand-name {
    font-weight: 600; color: var(--ink); letter-spacing: 1px; line-height: 1;
    display: flex; align-items: center; gap: 14px; white-space: nowrap;
  }
  .brand-name .dot { width: 22px; height: 22px; border-radius: 50%; background: var(--purple); flex: none; }
  .tagline { color: var(--purple); font-weight: 600; white-space: nowrap; }
  .tagline .lead { color: var(--ink-soft); font-weight: 400; }

  /* Appointment side */
  .appointment { padding: 30px 56px 0 62px; }
  .appointment__title {
    display: flex; align-items: flex-end; gap: 8px;
    font-size: 23px; font-weight: 700; color: var(--ink-soft); white-space: nowrap;
  }
  .appointment__title .accent { color: var(--purple); }
  .title-line { flex: 1; border-bottom: 2px dotted var(--dots); margin-bottom: 7px; margin-left: 4px; }
  .field-row {
    display: flex; align-items: flex-end; gap: 8px;
    margin-top: 20px; font-size: 18px; font-weight: 600; color: var(--purple); white-space: nowrap;
  }
  .dotline { flex: 1; border-bottom: 2px dotted var(--dots); margin-bottom: 6px; }
  .dotline--date { flex: 0 0 170px; }
  .dotline--time { flex: 0 0 130px; }
  .field-row .suffix { font-weight: 400; font-size: 16px; }
  .notice { margin-top: 20px; font-size: 17px; font-weight: 700; color: var(--ink-soft); white-space: nowrap; }
  .notice .accent { color: var(--purple); font-weight: 600; }
  .appointment .brand-name { position: absolute; left: 62px; bottom: 34px; font-size: 50px; }
  .appointment .tagline {
    position: absolute; right: 56px; bottom: 36px; text-align: right;
    font-size: 15px; line-height: 1.4;
  }

  /* Contact side */
  .contact .details {
    position: absolute; left: 372px; top: 46px; width: 300px;
    font-size: 17px; line-height: 1.3; color: var(--ink);
  }
  .person { font-size: 22px; font-weight: 700; color: var(--ink-soft); }
  .person .accent { color: var(--purple); }
  .role { font-size: 15px; margin-bottom: 20px; }
  .address { margin-bottom: 16px; }
  .contact-list { list-style: none; }
  .contact-list li { display: flex; align-items: center; gap: 12px; }
  .contact-list svg { width: 14px; height: 14px; fill: var(--purple); flex: none; }
  .contact .brand-name { position: absolute; left: 70px; bottom: 96px; font-size: 56px; }
  .contact .tagline { position: absolute; left: 106px; bottom: 60px; font-size: 18px; letter-spacing: .5px; }
</style>
</head>
<body>
<main class="sheet">

  <section class="card appointment" aria-label="Appointment card">
    <h2 class="appointment__title">Your Next <span class="accent">Appointment on</span><span class="title-line"></span></h2>
    <div class="field-row"><span class="label">Name :</span><span class="dotline"></span></div>
    <div class="field-row">
      <span class="label">Date :</span><span class="dotline dotline--date"></span>
      <span class="label">&nbsp;Time :</span><span class="dotline dotline--time"></span>
      <span class="suffix">AM / PM</span>
    </div>
    <div class="field-row">
      <span class="label">Date :</span><span class="dotline dotline--date"></span>
      <span class="label">&nbsp;Time :</span><span class="dotline dotline--time"></span>
      <span class="suffix">AM / PM</span>
    </div>
    <div class="field-row">
      <span class="label">Date :</span><span class="dotline dotline--date"></span>
      <span class="label">&nbsp;Time :</span><span class="dotline dotline--time"></span>
      <span class="suffix">AM / PM</span>
    </div>
    <p class="notice">If unable to keep appointment, <span class="accent">kindly give 24hrs notice.</span></p>
    <div class="brand-name"><span class="dot"></span>Gralo Tund</div>
    <p class="tagline"><span class="lead">Find your balance…</span><br>Relax, Renew, Revive</p>
  </section>

  <section class="card contact" aria-label="Contact card">
    <div class="details">
      <p class="person">Marcus <span class="accent">Hale</span></p>
      <p class="role">Managing Director</p>
      <p class="address">48 Linden Row<br>Hollowmere, 204815.</p>
      <ul class="contact-list">
        <li><svg viewBox="0 0 24 24" aria-hidden="true"><path d="M6.6 10.8a15 15 0 0 0 6.6 6.6l2.2-2.2a1 1 0 0 1 1-.25 11.4 11.4 0 0 0 3.6.57 1 1 0 0 1 1 1V20a1 1 0 0 1-1 1A17 17 0 0 1 3 4a1 1 0 0 1 1-1h3.5a1 1 0 0 1 1 1c0 1.25.2 2.45.57 3.57a1 1 0 0 1-.25 1z"/></svg>055-201 738 462</li>
        <li><svg viewBox="0 0 24 24" aria-hidden="true"><path d="M2 5h20v14H2zm2 2v.5l8 5 8-5V7l-8 5z"/></svg>care@gralotund.com</li>
        <li><svg viewBox="0 0 24 24" aria-hidden="true"><path d="M10.6 13.4a1 1 0 0 1 0-1.4l3-3a3 3 0 0 1 4.2 4.2l-2.5 2.5-1.4-1.4 2.5-2.5a1 1 0 0 0-1.4-1.4l-3 3a1 1 0 0 1-1.4 0zm2.8-2.8a1 1 0 0 1 0 1.4l-3 3a3 3 0 0 1-4.2-4.2l2.5-2.5 1.4 1.4-2.5 2.5a1 1 0 0 0 1.4 1.4l3-3a1 1 0 0 1 1.4 0z"/></svg>www.gralotund.com</li>
      </ul>
    </div>
    <div class="brand-name"><span class="dot"></span>Gralo Tund</div>
    <p class="tagline">Relax, Renew, Revive</p>
  </section>

</main>
</body>
</html>
```